Heritage Hollow Business Cards

Require a business card design. <br/><br/>Needs to include logo (either round or long version) plus these details:<br/>Maya Torvell<br/>Heritage Hollow<br/>maya@kelvadtrading.com.au<br/>02 6481 7395<br/>PO Box Glenwarra NSW 2791<br/>www.heritagehollow.com.au<br/><br/>I need in an editable format so that I can create for multiple staff members. <br/><br/>

Target Market(s)

We are an online store selling renovation products to home owners are builders. Looking for a classic classy design.

Industry/Entity Type

Home And Garden

Contact Information for Business Card

Maya Torvell
Heritage Hollow
maya@kelvadtrading.com.au
02 6481 7395
PO Box Glenwarra NSW 2791
www.heritagehollow.com.au

Colors

Designer to choose colors to be used in the design.

Requirements
Must have
• Must include Logo.

```html
<!DOCTYPE html>
<html lang="en">
<head>
<meta charset="utf-8">
<title>Heritage Hollow Business Cards</title>
<link href="https://fonts.googleapis.com/css2?family=Cormorant+Garamond:wght@600&family=Roboto:wght@300;400;500;700&display=swap" rel="stylesheet">
<style>
  :root {
    --backdrop: #e0e1e5;
    --front-card: #656565;
    --front-ink: #2e2e2e;
    --back-card: #ececec;
    --ink: #1f1f1f;
    --ink-soft: #3a3a3a;
    --rule: #8a8a8a;
    --arc: #cfcfcf;
  }
  * { margin: 0; padding: 0; box-sizing: border-box; }
  html, body {
    width: 1200px; height: 1200px; overflow: hidden;
    background: var(--backdrop);
    font-family: "Roboto", Arial, sans-serif;
  }
  .card {
    position: absolute;
    left: 272px;
    width: 657px;
    height: 378px;
    border-radius: 11px;
    overflow: hidden;
  }
  .card-front { top: 180px; background: var(--front-card); }
  .card-back { top: 643px; background: var(--back-card); }

  .brand {
    position: absolute;
    left: 104px; top: 120px;
    display: flex; align-items: center; gap: 22px;
  }
  .brand-dot {
    width: 104px; height: 104px;
    border: 2px solid var(--front-ink);
    border-radius: 50%;
  }
  .brand-name {
    font-family: "Cormorant Garamond", Georgia, serif;
    font-weight: 600;
    font-size: 66px;
    color: var(--front-ink);
    letter-spacing: 0.5px;
  }

  .back-arc { position: absolute; inset: 0; }

  .contact { position: absolute; left: 43px; top: 196px; width: 240px; }
  .person-name {
    font-family: "Cormorant Garamond", Georgia, serif;
    font-weight: 600;
    font-size: 28px;
    line-height: 32px;
    color: var(--ink-soft);
    letter-spacing: 0.3px;
  }
  .rule { width: 187px; height: 1px; background: var(--rule); }
  .rule-top { margin-top: 8px; }
  .company { font-weight: 500; font-size: 15.5px; color: var(--ink); margin-top: 6px; line-height: 18px; }
  .address { font-weight: 300; font-size: 12px; color: var(--ink); margin-top: 2px; line-height: 16px; }
  .rule-mid { margin-top: 6px; }
  .details { list-style: none; margin-top: 6px; }
  .details li {
    display: flex; align-items: center; gap: 6px;
    font-weight: 300; font-size: 12px; line-height: 19px; color: var(--ink);
  }
  .details svg { width: 10px; height: 10px; flex: none; }
  .details b { font-weight: 500; }
</style>
</head>
<body>

<section class="card card-front" aria-label="Business card front">
  <div class="brand">
    <span class="brand-dot"></span>
    <span class="brand-name">Heritage Hollow</span>
  </div>
</section>

<section class="card card-back" aria-label="Business card back">
  <svg class="back-arc" width="657" height="378" viewBox="0 0 657 378" aria-hidden="true">
    <circle cx="660" cy="238" r="292" fill="none" stroke="var(--arc)" stroke-width="2"/>
  </svg>

  <div class="contact">
    <h1 class="person-name">MAYA TORVELL</h1>
    <div class="rule rule-top"></div>
    <p class="company">Heritage Hollow</p>
    <p class="address">PO Box Glenwarra NSW 2791</p>
    <div class="rule rule-mid"></div>
    <ul class="details">
      <li>
        <svg viewBox="0 0 24 24"><path fill="#222" d="M6.6 10.8a15 15 0 0 0 6.6 6.6l2.2-2.2a1 1 0 0 1 1-.25 11.4 11.4 0 0 0 3.6.57 1 1 0 0 1 1 1V20a1 1 0 0 1-1 1A17 17 0 0 1 3 4a1 1 0 0 1 1-1h3.5a1 1 0 0 1 1 1c0 1.25.2 2.45.57 3.57a1 1 0 0 1-.25 1z"/></svg>
        02 6481 7395
      </li>
      <li>
        <svg viewBox="0 0 24 24"><path fill="#222" d="M3 5h18v14H3zm2 2v.5l7 4.5 7-4.5V7zm0 2.9V17h14V9.9l-7 4.5z"/></svg>
        maya@kelvadtrading.com.au
      </li>
      <li>
        <svg viewBox="0 0 24 24"><g fill="none" stroke="#222" stroke-width="2"><circle cx="12" cy="12" r="9"/><path d="M3 12h18M12 3c3 3 3 15 0 18M12 3c-3 3-3 15 0 18"/></g></svg>
        <span>www.<b>heritagehollow</b>.com.au</span>
      </li>
    </ul>
  </div>
</section>

</body>
</html>
```